2018 Desk Calendar Design with Better Spine, Better Health with Chiropractic

In conjunction with the Federation of Spinal Wellness Malaysia (FSW), we are organizing a 2018 desk calendar design. The cover page and monthly design size is 210mm (H) x 195mm (W). The will be a total of 27 designs including a cover page (front) [Sample 1], cover page (back) Malaysia National & States Holiday 2018 (https://restdaylist.example.my/2018-dates/) [Sample 2], 12 months design (front) [Sample 3 and 4], 12 months design (back) [Sample 5], Last page (2017 and 2019 calendar) [Sample 6].

Below are some recommendations for monthly back cover design. The main theme remain as Better SPINE, Better HEALTH with CHIROPRACTIC. Each month can in collaborate with of the following element:-

Suggestion 1 (Celebration of the Month)
January - New Year
February - Chinese New Year
March -
April -
May - Labour Day
June - Aidilfitri Festival
July-
August - Independent Day
September - Malaysia Day
October - World Spine Day
November - Deepavali Festival
December - Christmas

Suggestion 2 (States in Malaysia)
January - Perlis
February - Kedah
March - Penang
April - Perak
May - Selangor
June - Negeri Sembilan
July- Melaka
August - Johor
September - Pahang
October - Terengganu
November - Kelantan
December - Sabah & Sarawak

Target Market(s)

Chiropractors and Public

Industry/Entity Type

Chiropractor

Colors

Designer to choose colors to be used in the design.

Requirements
Must have
• The theme for the desk calendar design is Better Spine, Better Health with Chiropractic.
• The cover page should include 5th Anniversary element.
Nice to have
• Lunar or Islamic calendar is optional in the Gregorian calendar.
• AI Format
• Footnote of each page www.spinefsw.example.org

```html
<!DOCTYPE html>
<html lang="en">
<head>
<meta charset="utf-8">
<title>August 2018 – Federation of Spinal Wellness Malaysia Desk Calendar</title>
<link rel="stylesheet" href="https://fonts.googleapis.com/css2?family=Michroma&family=Noto+Serif:wght@700&family=Roboto:wght@400&display=swap">
<style>
  :root {
    --page-bg: #b8bfcc;
    --ink: #111111;
    --sunday: #e0242b;
    --rule: #1c1c4a;
    --navy: #161548;
    --swoosh: #3f6cb8;
    --swoosh-light: #6f93d2;
    --fact: #ffffff;
    --photo-light: #e4e7ec;
    --photo-mid: #a9b6c6;
    --photo-accent: #3b9ccc;
  }
  * { margin: 0; padding: 0; box-sizing: border-box; }
  html, body { width: 1111px; height: 1200px; overflow: hidden; background: var(--page-bg); }
  .calendar-page {
    position: relative;
    width: 1111px;
    height: 1200px;
    background: var(--page-bg);
    overflow: hidden;
    font-family: "Michroma", sans-serif;
    color: var(--ink);
  }
  .artwork { position: absolute; inset: 0; width: 1111px; height: 1200px; }
  .month-grid .cell, .mini-month .cell {
    position: absolute;
    line-height: 1;
    white-space: nowrap;
  }
  .month-grid .cell { font-size: 28px; transform: translateY(-100%); }
  .month-grid .weekday { font-size: 25px; }
  .month-grid .sun, .mini-month .sun { color: var(--sunday); }
  .month-grid .rule {
    position: absolute;
    left: 207px;
    width: 890px;
    height: 2px;
    background: var(--rule);
  }
  .mini-month .cell { font-size: 14px; transform: translateY(-100%); }
  .mini-month .mini-title { font-size: 17px; letter-spacing: 2px; }
  .anniversary-badge {
    position: absolute;
    left: 519px;
    top: 581px;
    width: 96px;
    height: 96px;
    border-radius: 50%;
    background: #c9cfdb;
    border: 3px solid #2e3d9c;
  }
  .spine-fact {
    position: absolute;
    right: 416px;
    top: 1080px;
    text-align: right;
    font-family: "Noto Serif", serif;
    font-weight: 700;
    font-size: 30px;
    line-height: 39px;
    color: var(--fact);
  }
  .site-footnote {
    position: absolute;
    left: 24px;
    top: 1166px;
    font-family: "Roboto", sans-serif;
    font-size: 17px;
    color: #1a1a1a;
  }
</style>
</head>
<body>
<main class="calendar-page">

  <svg class="artwork" viewBox="0 0 1111 1200" xmlns="http://www.w3.org/2000/svg">
    <defs>
      <linearGradient id="photoTone" x1="0" y1="0" x2="1" y2="1">
        <stop offset="0" stop-color="var(--photo-mid)"/>
        <stop offset="0.45" stop-color="var(--photo-light)"/>
        <stop offset="0.7" stop-color="var(--photo-accent)"/>
        <stop offset="1" stop-color="var(--photo-light)"/>
      </linearGradient>
    </defs>
    <path class="treatment-photo" role="img" aria-label="Photo of a chiropractor adjusting a patient's back"
          d="M0,640 C250,700 550,820 800,960 C950,1040 1050,1110 1111,1170 L1111,1200 L0,1200 Z"
          fill="url(#photoTone)"/>
    <path class="swoosh-band" d="M0,610 C300,670 600,810 850,970 C980,1050 1060,1115 1111,1155"
          fill="none" stroke="var(--swoosh)" stroke-width="44" opacity="0.9"/>
    <path class="swoosh-highlight" d="M0,585 C300,645 600,785 850,945 C980,1025 1060,1090 1111,1130"
          fill="none" stroke="var(--swoosh-light)" stroke-width="10" opacity="0.7"/>
    <path class="spine-column" role="img" aria-label="Illustration of spinal vertebrae along the curve"
          d="M10,560 C300,630 560,770 800,920 C950,1010 1060,1100 1111,1185"
          fill="none" stroke="var(--navy)" stroke-width="62"/>
    <text class="month-title" x="668" y="661" textLength="400" lengthAdjust="spacingAndGlyphs"
          font-family="Michroma, sans-serif" font-size="66" fill="var(--navy)">AUGUST</text>
  </svg>

  <section class="month-grid" aria-label="August 2018">
    <span class="cell weekday" style="left:210px;top:110px">M</span>
    <span class="cell weekday" style="left:339px;top:110px">T</span>
    <span class="cell weekday" style="left:469px;top:110px">W</span>
    <span class="cell weekday" style="left:598px;top:110px">T</span>
    <span class="cell weekday" style="left:728px;top:110px">F</span>
    <span class="cell weekday" style="left:858px;top:110px">S</span>
    <span class="cell weekday sun" style="left:987px;top:110px">S</span>

    <span class="cell" style="left:469px;top:190px">1</span>
    <span class="cell" style="left:598px;top:190px">2</span>
    <span class="cell" style="left:728px;top:190px">3</span>
    <span class="cell" style="left:858px;top:190px">4</span>
    <span class="cell sun" style="left:987px;top:190px">5</span>
    <div class="rule" style="top:196px"></div>

    <span class="cell" style="left:210px;top:284px">6</span>
    <span class="cell" style="left:339px;top:284px">7</span>
    <span class="cell" style="left:469px;top:284px">8</span>
    <span class="cell" style="left:598px;top:284px">9</span>
    <span class="cell" style="left:728px;top:284px">10</span>
    <span class="cell" style="left:858px;top:284px">11</span>
    <span class="cell sun" style="left:987px;top:284px">12</span>
    <div class="rule" style="top:290px"></div>

    <span class="cell" style="left:210px;top:379px">13</span>
    <span class="cell" style="left:339px;top:379px">14</span>
    <span class="cell" style="left:469px;top:379px">15</span>
    <span class="cell" style="left:598px;top:379px">16</span>
    <span class="cell" style="left:728px;top:379px">17</span>
    <span class="cell" style="left:858px;top:379px">18</span>
    <span class="cell sun" style="left:987px;top:383px">19</span>
    <div class="rule" style="top:385px"></div>

    <span class="cell" style="left:210px;top:478px">20</span>
    <span class="cell" style="left:339px;top:478px">21</span>
    <span class="cell" style="left:469px;top:478px">22</span>
    <span class="cell" style="left:598px;top:478px">23</span>
    <span class="cell" style="left:728px;top:478px">24</span>
    <span class="cell" style="left:858px;top:478px">25</span>
    <span class="cell sun" style="left:987px;top:478px">26</span>
    <div class="rule" style="top:484px"></div>

    <span class="cell" style="left:210px;top:571px">27</span>
    <span class="cell" style="left:339px;top:571px">28</span>
    <span class="cell" style="left:469px;top:571px">29</span>
    <span class="cell" style="left:598px;top:571px">30</span>
    <span class="cell" style="left:728px;top:571px">31</span>
    <div class="rule" style="top:575px"></div>
  </section>

  <div class="anniversary-badge" aria-hidden="true"></div>

  <section class="mini-month" aria-label="July 2018">
    <span class="cell mini-title" style="left:931px;top:707px">JULY</span>
    <span class="cell" style="left:842px;top:738px">M</span>
    <span class="cell" style="left:876px;top:738px">T</span>
    <span class="cell" style="left:915px;top:738px">W</span>
    <span class="cell" style="left:951px;top:738px">T</span>
    <span class="cell" style="left:989px;top:738px">F</span>
    <span class="cell" style="left:1026px;top:738px">S</span>
    <span class="cell sun" style="left:1062px;top:738px">S</span>

    <span class="cell" style="left:842px;top:760px">30</span>
    <span class="cell" style="left:876px;top:760px">31</span>
    <span class="cell sun" style="left:1062px;top:760px">1</span>

    <span class="cell" style="left:842px;top:790px">2</span>
    <span class="cell" style="left:876px;top:790px">3</span>
    <span class="cell" style="left:915px;top:790px">4</span>
    <span class="cell" style="left:951px;top:790px">5</span>
    <span class="cell" style="left:989px;top:790px">6</span>
    <span class="cell" style="left:1026px;top:790px">7</span>
    <span class="cell sun" style="left:1062px;top:790px">8</span>

    <span class="cell" style="left:842px;top:821px">9</span>
    <span class="cell" style="left:876px;top:821px">10</span>
    <span class="cell" style="left:915px;top:821px">11</span>
    <span class="cell" style="left:951px;top:821px">12</span>
    <span class="cell" style="left:989px;top:821px">13</span>
    <span class="cell" style="left:1026px;top:821px">14</span>
    <span class="cell sun" style="left:1062px;top:821px">15</span>

    <span class="cell" style="left:842px;top:851px">16</span>
    <span class="cell" style="left:876px;top:851px">17</span>
    <span class="cell" style="left:915px;top:851px">18</span>
    <span class="cell" style="left:951px;top:851px">19</span>
    <span class="cell" style="left:989px;top:851px">20</span>
    <span class="cell" style="left:1026px;top:851px">21</span>
    <span class="cell sun" style="left:1062px;top:851px">22</span>

    <span class="cell" style="left:842px;top:882px">23</span>
    <span class="cell" style="left:876px;top:882px">24</span>
    <span class="cell" style="left:915px;top:882px">25</span>
    <span class="cell" style="left:951px;top:882px">26</span>
    <span class="cell" style="left:989px;top:882px">27</span>
    <span class="cell" style="left:1026px;top:882px">28</span>
    <span class="cell sun" style="left:1062px;top:882px">29</span>
  </section>

  <p class="spine-fact">Spine Fact:<br>There are about 220<br>ligaments in the spine.</p>

  <p class="site-footnote">www.spinefsw.example.org</p>
</main>
</body>
</html>
```